Clean business card with logo provided

I want a card that will stand out among the masses. I need the color and image to show professionalism and yet have a family appeal showing that I only deal with win/win scenarios. The back of the card will be used to take notes about the individual so I can use that in my database entry. I like modern design but need professionalism in it also. It needs to fit my "clean, safe, and affordable housing" motto. I need to be able to write on the file and update the card details for my employees.

Target Market(s)

Investors looking to make investment income through real estate

Industry/Entity Type

Real Estate

Contact Information for Business Card

Brent Kovalich
blank address, city, st, zip code
480-555-3174
brentkovalich@ridgeworthrentals.example
www.ridgeworthrentals.example

Font styles to use
Sans Serif

Requirements
Must have
• I would like the back of the card to have lines for info. example
• Met/Visited: Date:
• Interets:
Nice to have
• I want the cards color to match the logo background color. Font with details to be san serif and black. I want the card rectangular with square corners. Standard business card size. I would like to see cards designed with both images to see which i prefer more.

```html
<!DOCTYPE html>
<html lang="en">
<head>
<meta charset="utf-8">
<title>Ridgeworth Rentals LLC — Business Card</title>
<link rel="stylesheet" href="https://fonts.googleapis.com/css2?family=Marcellus&family=Open+Sans:wght@400;600&display=swap">
<style>
  :root {
    --page-bg: #8e8e8e;
    --card-black: #000000;
    --brand-teal: #1aa0b8;
    --band-teal: #0b9cb6;
    --paper: #e9eaec;
    --text-light: #e6e6e6;
    --ink: #111111;
    --rule: #2a2a2a;
    --art-light: #e4e4e6;
  }
  * { box-sizing: border-box; margin: 0; padding: 0; }
  html, body { width: 1105px; height: 1200px; overflow: hidden; }
  body { background: var(--page-bg); position: relative; font-family: "Open Sans", Arial, sans-serif; }

  .card { position: absolute; left: 182px; width: 747px; height: 427px; overflow: hidden; }
  .card--front { top: 119px; background: var(--card-black); }
  .card--back { top: 637px; background: var(--paper); }

  .brand-name { font-family: "Marcellus", Georgia, serif; font-weight: 400; letter-spacing: 1px; white-space: nowrap; }
  .brand-tagline { font-family: "Open Sans", Arial, sans-serif; white-space: nowrap; }

  /* Front */
  .front-brand { position: absolute; left: 46px; top: 64px; z-index: 1; }
  .front-brand .brand-name { color: var(--brand-teal); font-size: 23px; }
  .front-brand .brand-tagline { color: var(--brand-teal); font-size: 10.5px; margin-top: 8px; letter-spacing: 0.2px; }

  .holder-name { position: absolute; left: 46px; top: 180px; z-index: 1; font-family: "Marcellus", Georgia, serif; font-weight: 400; color: var(--brand-teal); font-size: 26px; letter-spacing: 1px; text-transform: uppercase; white-space: nowrap; }
  .address { position: absolute; left: 46px; top: 228px; z-index: 1; color: var(--text-light); font-size: 19px; line-height: 27px; white-space: nowrap; }
  .contact-list { position: absolute; left: 46px; top: 298px; z-index: 1; list-style: none; color: var(--text-light); font-size: 17px; }
  .contact-list li { display: flex; align-items: center; height: 28px; white-space: nowrap; }
  .contact-list svg { width: 15px; height: 15px; margin-right: 11px; flex: none; }

  .feature-art { position: absolute; left: 440px; top: 0; width: 307px; height: 427px;
    background: linear-gradient(100deg, var(--card-black) 0%, var(--card-black) 22%, #3a3a3c 42%, var(--art-light) 75%, var(--art-light) 100%); }

  /* Back */
  .back-band { position: absolute; left: 0; top: 0; width: 100%; height: 210px; background: var(--band-teal); }
  .back-brand { position: absolute; left: 0; right: 0; top: 70px; text-align: center; }
  .back-brand .brand-name { color: var(--ink); font-size: 30px; }
  .back-brand .brand-tagline { color: var(--ink); font-size: 11px; font-weight: 600; margin-top: 10px; }

  .note-label { position: absolute; color: var(--brand-teal); font-size: 18px; text-transform: uppercase; white-space: nowrap; }
  .note-rule { position: absolute; height: 0; border-top: 1.5px solid var(--rule); }
</style>
</head>
<body>

  <section class="card card--front" aria-label="Business card front">
    <div class="feature-art" role="img" aria-label="Large light grey illustration of a gliding ray seen from above"></div>

    <div class="front-brand">
      <div class="brand-name">RIDGEWORTH RENTALS LLC</div>
      <div class="brand-tagline">Providing clean, safe, and affordable housing</div>
    </div>

    <h1 class="holder-name">Brent Kovalich</h1>
    <p class="address">4120 Alder Crest Way<br>Anchorage, Alaska 34518</p>

    <ul class="contact-list">
      <li>
        <svg viewBox="0 0 16 16" aria-hidden="true"><path fill="#1aa0b8" d="M3.6 1.2l2.3 2.6-1.2 1.9c.9 2 2.5 3.6 4.5 4.6l1.9-1.2 2.6 2.3-1.2 2.7C7.3 14 2 8.7 1 2.4z"/></svg>
        480-555-3174
      </li>
      <li>
        <svg viewBox="0 0 16 16" aria-hidden="true"><rect x="1" y="3" width="14" height="10" fill="#1aa0b8"/><path d="M1.5 3.5L8 9l6.5-5.5" fill="none" stroke="#000" stroke-width="1.3"/></svg>
        brentkovalich@ridgeworthrentals.example
      </li>
      <li>
        <svg viewBox="0 0 16 16" aria-hidden="true"><circle cx="8" cy="8" r="7" fill="#1aa0b8"/><path d="M1 8h14M8 1c-3 3.5-3 10.5 0 14M8 1c3 3.5 3 10.5 0 14" fill="none" stroke="#000" stroke-width="1"/></svg>
        www.ridgeworthrentals.example
      </li>
    </ul>
  </section>

  <section class="card card--back" aria-label="Business card back">
    <div class="back-band">
      <div class="back-brand">
        <div class="brand-name">RIDGEWORTH RENTALS LLC</div>
        <div class="brand-tagline">Providing clean, safe, and affordable housing</div>
      </div>
    </div>

    <span class="note-label" style="left:55px; top:268px;">Met/Visited:</span>
    <span class="note-rule" style="left:188px; top:290px; width:254px;"></span>
    <span class="note-label" style="left:452px; top:268px;">Date:</span>
    <span class="note-rule" style="left:532px; top:290px; width:152px;"></span>

    <span class="note-label" style="left:55px; top:321px;">Interets:</span>
    <span class="note-rule" style="left:160px; top:343px; width:524px;"></span>

    <span class="note-rule" style="left:61px; top:391px; width:623px;"></span>
  </section>

</body>
</html>
```